Flyer für Verkauf von Radondetektoren
Zielgruppe
Ich verkaufe Radondetektoren zur Messung von Radon in Innenräumen. Zielgruppe sind Privatpersonen, Firmen, Genossenschaften und andere Hauseigentümer.
Aufgabenstellung
Ich brauche das Design für meine Messanleitung.
Kreativ - modern - weniger kann mehr sein
Struktur ist wichtigt, es soll also einfach sein zu lesen und zu verstehen, was gemacht werden soll. Können Bulletpoints, Icons mit eingebracht werden.
Wichtig ist auch, dass die beiden Logos 'Luftprüfer.de' und TESTOVAL' auf der Messanleitung vorhanden sind. Wobei 'Luftprüfer.de' das Hauptlogo ist.
DIN format dachte ich A4 beidseitig (Text müsste also auf diese Grösse angepasst werden).
Kann natürlich auch Flyer-Format sein oder andere Vorschläge!
Bildmaterial gibt es auf unsere Homepage https://luftprüfer.de und https://luftkontroll.se . Diese haben wir bereits gekauft und können verwendet werden. Ich lade sie den bei Bedarf hoch. Es können natürlich auch andere Vorschläge kommen.

```html
<!DOCTYPE html>
<html lang="de">
<head>
<meta charset="utf-8">
<title>Messanleitung – Luftprüfer.de</title>
<link href="https://fonts.googleapis.com/css2?family=Open+Sans:ital,wght@0,400;0,600;0,700;1,400&family=Poppins:wght@400;500;600&display=swap" rel="stylesheet">
<style>
  :root{
    --red:#d3272e;
    --red-soft:rgba(214,72,60,.82);
    --ink:#3d3d3d;
    --page:#f5f5f5;
    --page-grey:#e6e6e6;
    --stage:#ececec;
    --accent-yellow:#e0a416;
    --partner-blue:#1f4fa0;
  }
  *{box-sizing:border-box;margin:0;padding:0}
  html,body{width:1200px;height:800px;overflow:hidden}
  body{background:var(--stage);font-family:"Open Sans",Arial,sans-serif;color:var(--ink);position:relative}
  .page{position:absolute;top:15px;width:545px;height:770px;background:var(--page);overflow:hidden;box-shadow:0 6px 18px rgba(0,0,0,.12)}
  .page--front{left:38px}
  .page--back{left:617px}
  p,li{font-size:6.6px;line-height:12.6px}
  ul{list-style:none}
  .bullets li{position:relative;padding-left:14px;margin-bottom:6px}
  .bullets li::before{content:"";position:absolute;left:0;top:3.3px;width:6px;height:6px;border-radius:50%;background:var(--red)}
  .hl,.link{color:var(--red);font-weight:700}

  /* front */
  .hero{position:absolute;left:0;top:0;width:100%;height:236px;
    background:linear-gradient(120deg,#d9c3b2 0%,#e8d6c6 30%,#c9a58a 55%,#e6c49a 80%,#f1e3cf 100%)}
  .brand{position:absolute;right:14px;top:22px;display:flex;align-items:center;gap:6px}
  .brand__dot{width:16px;height:16px;border-radius:50%;background:var(--accent-yellow)}
  .brand__name{font-family:"Poppins",sans-serif;font-size:22px;font-weight:400;color:#2b2b2b;line-height:1}
  .title-band{position:absolute;left:0;top:134px;width:362px;height:90px;background:var(--red-soft);padding:7px 26px;color:#fff}
  .title-band h1{font-family:"Poppins",sans-serif;font-weight:600;font-size:23px;letter-spacing:.3px;line-height:30px}
  .title-band p{font-family:"Poppins",sans-serif;font-size:12px;line-height:22px;letter-spacing:.2px}
  .front-body{position:absolute;top:258px;left:26px;right:16px;display:flex}
  .col-left{width:237px}
  .divider{width:2px;background:var(--red);margin:10px 17px 0 9px;height:455px}
  .col-right{flex:1}
  .step{display:flex;align-items:center;gap:7px;margin-bottom:6px}
  .step__icon{flex:none;width:26px;height:26px;border:2px solid var(--red);border-radius:50%;color:var(--red);font-family:"Poppins",sans-serif;font-size:11px;font-weight:600;display:flex;align-items:center;justify-content:center;line-height:1}
  .step__num{font-family:"Poppins",sans-serif;font-size:10.5px;color:var(--red);font-weight:500;line-height:13px}
  .step__title{font-family:"Poppins",sans-serif;font-size:8px;font-weight:600;color:#222;line-height:11px}
  .note{font-style:italic}
  .step-block{margin-bottom:14px}
  .section-title{font-family:"Poppins",sans-serif;font-size:13.5px;font-weight:500;color:#222;border-left:2px solid var(--red);padding-left:6px;margin:16px 0 14px}
  .sub{display:flex;align-items:center;justify-content:space-between;margin:10px 0 8px}
  .sub h3{font-family:"Open Sans",sans-serif;font-size:8.6px;font-weight:700;color:var(--red);line-height:12.5px}
  .front-foot{position:absolute;left:0;bottom:0;width:100%;height:13px;background:var(--red)}

  /* back */
  .back-top{position:absolute;top:0;left:0;right:0;height:575px;padding:24px 26px 0 28px}
  .back-head{display:flex;justify-content:space-between;align-items:flex-start;margin-bottom:12px}
  .back-head h2{font-family:"Poppins",sans-serif;font-size:13.5px;font-weight:500;color:#222;line-height:18px;border-left:2px solid var(--red);padding-left:6px}
  .partner{display:flex;align-items:center;gap:6px;margin-top:4px}
  .partner__dot{width:16px;height:16px;border-radius:50%;background:var(--partner-blue)}
  .partner__name{font-family:"Open Sans",sans-serif;font-size:21px;color:var(--partner-blue);font-weight:400;letter-spacing:.5px}
  .two{display:flex;gap:24px}
  .two>*{flex:1}
  .intro{margin:4px 0 10px}
  .mcols{display:flex}
  .mcols .mcol{flex:1}
  .mcols .vline{width:2px;background:var(--red);margin:0 16px 0 10px}
  .mcol h4{font-size:9px;font-weight:700;color:var(--red);margin-bottom:6px}
  .mcol .bullets li{margin-bottom:2px}
  .address{display:flex;align-items:center;gap:10px;margin:6px 0 8px}
  .address p{font-size:7.4px;line-height:14px;color:var(--red);font-weight:700}
  .back-grey{position:absolute;top:575px;left:0;right:0;bottom:40px;background:var(--page-grey);padding:14px 26px}
  .tips{border:2px solid var(--red);padding:8px 16px;height:138px}
  .tips h4{font-size:9px;font-weight:700;color:var(--red);margin-bottom:6px}
  .back-foot{position:absolute;left:0;right:0;bottom:0;height:40px;background:var(--red);color:#fff;font-size:7.6px;font-weight:700;display:flex;align-items:center;justify-content:center}
</style>
</head>
<body>

<section class="page page--front">
  <div class="hero" role="img" aria-label="Foto einer fröhlichen Familie beim Einzug mit Umzugskartons"></div>
  <div class="brand"><span class="brand__dot"></span><span class="brand__name">Luftprüfer.de</span></div>
  <div class="title-band">
    <h1>MESSANLEITUNG</h1>
    <p>FÜR RADONMESSUNGEN VON INNENRAUMLUFT<br>MIT PASSIVEN RADON DETEKTOREN</p>
  </div>

  <div class="front-body">
    <div class="col-left">
      <div class="step-block">
        <div class="step">
          <span class="step__icon">1</span>
          <div><div class="step__num">SCHRITT 1:</div><div class="step__title">REGISTRIERUNG UND ANMELDUNG</div></div>
        </div>
        <p>Wenn Sie Neukunde sind, legen Sie bitte zunächst ein neues Benutzerkonto auf unserem Online-Portal <span class="link">https://kundenportal.testoval.se/de an.</span> Anschließend können Sie die Radondetektoren registrieren. Vermerken Sie den Start der Messung (Datum und Uhrzeit), die Messorte (Raum und Etage) sowie die 9-stellige Seriennummer der Detektoren, die Sie auf der Verpackung oder auf der Unterseite der jeweiligen Detektoren finden.</p>
        <p class="note" style="margin-top:4px">Firmenkunden haben die Möglichkeit eine Excel-Datei als Hilfsmittel herunterzuladen, die Sie ausfüllen und dann wieder hochladen.</p>
      </div>
      <div class="step-block">
        <div class="step">
          <span class="step__icon">2</span>
          <div><div class="step__num">SCHRITT 2:</div><div class="step__title">PLATZIERUNG DER DETEKTOREN</div></div>
        </div>
        <p>Bevor Sie die Detektoren der Verpackung entnehmen, überlegen Sie wo genau Sie die Radondetektoren platzieren wollen. Die Radonmessung beginnt, sobald Sie die radondichten Verpackungen öffnen. Beachten Sie bei der Platzierung zunächst die <span class="hl">Auswahl der Räume</span> und <span class="hl">die Positionierung der Radondetektoren im Raum.</span> Für eine zuverlässige Radonmessung empfehlen wir wie folgt vorzugehen:</p>
      </div>
      <h2 class="section-title">Die Auswahl der Räume:</h2>
      <div class="sub"><h3>Radonmessungen für Einfamilienhäuser:</h3>
        <svg width="28" height="26" viewBox="0 0 28 26" fill="none" stroke="#d3272e" stroke-width="1.4"><path d="M3 12 L14 3 L25 12"/><rect x="6" y="11" width="16" height="13"/><rect x="11" y="16" width="6" height="8"/></svg></div>
      <ul class="bullets">
        <li>Es sollten mindestens zwei Wohnräume und pro bewohnte Etage mindestens ein Wohnraum gemessen werden. Wählen Sie Räume aus, in denen Sie sich oft aufhalten (z.B. das Wohn- und Schlafzimmer). Vermeiden Sie aber Räume, in denen das Fenster mehrere Stunden am Tag oder in der Nacht geöffnet ist.</li>
      </ul>
    </div>
    <div class="divider"></div>
    <div class="col-right">
      <ul class="bullets" style="margin-top:12px">
        <li>Insofern Sie einen Keller haben, empfehlen wir alle Kellerräume zu messen, da hier meist das größte Risiko einer erhöhten Radonkonzentration erwartet wird.</li>
      </ul>
      <div class="sub"><h3>Radonmessungen für Mehrfamilienhäuser,<br>Wohnungen und Wohnkomplexen:</h3>
        <svg width="28" height="30" viewBox="0 0 28 30" fill="none" stroke="#d3272e" stroke-width="1.4"><rect x="5" y="3" width="18" height="25"/><path d="M9 8h10M9 13h10M9 18h10M9 23h10"/></svg></div>
      <ul class="bullets">
        <li>Alle Wohnungen mit direktem Bodenkontakt sowie mindestens eine Wohnung pro Etage sollten gemessen werden. Wählen Sie dabei Wohnungen, die an Aufzügen oder Luftschächten liegen.</li>
        <li>In größeren Wohnkomplexen sollten insgesamt mindestens 20% aller Wohnungen in einem Gebäude gemessen werden.</li>
        <li>Es sollten mindestens zwei Wohnräume pro ausgewählte Wohnung gemessen werden. Wählen Sie Räume aus, in denen Sie sich oft aufhalten (z.B. das Wohn- und Schlafzimmer). Vermeiden Sie aber Räume, in denen das Fenster mehrere Stunden am Tag oder in der Nacht geöffnet ist.</li>
        <li>Selbst bei einer Einzimmerwohnung sollten Sie zwei Detektoren aufstellen.</li>
      </ul>
      <div class="sub"><h3>Radonmessungen für Arbeitsplätze und<br>öffentliche Gebäude:</h3>
        <svg width="28" height="28" viewBox="0 0 28 28" fill="none" stroke="#d3272e" stroke-width="1.4"><path d="M3 10 L14 3 L25 10 Z"/><path d="M6 11v13M11 11v13M17 11v13M22 11v13M3 25h22"/></svg></div>
      <ul class="bullets">
        <li>Wählen Sie Räume, die regelmäßig mehr als vier Stunden pro Tag genutzt werden.</li>
        <li>Messen Sie alle unterirdischen Räumlichkeiten, da hier meist das größte Risiko einer erhöhten Radonkonzentration erwartet wird.</li>
        <li>Messen Sie alle Räume im Erdgeschoß. Für größere Räumlichkeiten empfehlen wir einen Detektor pro 200 m².</li>
        <li>In den oberen Etagen sollten Sie mit mindestens zwei Detektoren, sowie mindestens einem Detektor pro 200 m² messen.</li>
      </ul>
    </div>
  </div>
  <div class="front-foot"></div>
</section>

<section class="page page--back">
  <div class="back-top">
    <div class="back-head">
      <h2>Platzierung der Detektoren<br>im Raum:</h2>
      <div class="partner"><span class="partner__dot"></span><span class="partner__name">testoval</span></div>
    </div>
    <div class="two">
      <ul class="bullets">
        <li>Platzieren Sie die Detektoren in einem Mindestabstand von 20 cm zu Wänden, 50 cm zu Abluftsventilen, sowie 1,50 m zu Fenstern, Außentüren, Zuluftsventilen und Heizkörpern.</li>
        <li>Stellen Sie die Detektoren nicht auf dem Boden, an starken Wärmequellen oder Luftströmen auf. Vermeiden Sie auch Räume mit hoher Luftfeuchtigkeit, wie zum Beispiel das Badezimmer.</li>
      </ul>
      <ul class="bullets">
        <li>Die Detektoren können entweder stehend (auf einem Tisch, im Regal oder einer Schrankwand) oder hängend mitten im Raum (z.B. von einer Lampe) platziert werden.</li>
        <li>Stellen Sie die Detektoren während der gesamten Messdauer nicht um.</li>
        <li>Versuchen Sie nicht das Gehäuse der Detektoren zu öffnen und platzieren Sie diese immer außer Reichweite von Kindern.</li>
      </ul>
    </div>

    <div class="step" style="margin-top:4px">
      <span class="step__icon">3</span>
      <div><div class="step__num">SCHRITT 3:</div><div class="step__title">RADONMESSUNG</div></div>
    </div>
    <p class="intro">Die Radonmessung beginnt, sobald Sie die radondichten Verpackungen öffnen. <span style="color:var(--red)">Bitte halten Sie die Messdauer wie folgt ein:</span></p>
    <div class="mcols">
      <div class="mcol">
        <h4>Kurzzeitmessung:</h4>
        <ul class="bullets">
          <li>Mindestmessdauer 10 Tage (bis hin zu 30 Tagen).</li>
          <li>Führen Sie die Messung vorzugsweise in der Heizperiode (1. Oktober – 30. April) durch.</li>
          <li>Kurzzeitmessungen werden oft beim Kauf oder Verkauf von Immobilien genutzt, um ein mögliches Gefährdungspotential abschätzen zu können, oder wenn die Zeit nicht ausreicht, um eine Langzeitmessung durchzuführen.</li>
        </ul>
      </div>
      <div class="vline"></div>
      <div class="mcol">
        <h4>Langzeitmessung:</h4>
        <ul class="bullets">
          <li>Mindestmessdauer 3 Monate während der Heizperiode (1. Oktober – 30. April).</li>
          <li>Um einen Jahresmittelwert der Radonkonzentration in Innenräumen ermitteln zu können, halten Sie die Messdauer von 12 Monaten ein.</li>
          <li>Falls Ihr Arbeitsplatz in einem Radon-Vorsorgegebiet liegt und somit der Messpflicht unterliegt, muss die Messdauer von 12 Monaten eingehalten werden.</li>
        </ul>
      </div>
    </div>

    <div class="step" style="margin-top:8px">
      <span class="step__icon">4</span>
      <div><div class="step__num">SCHRITT 4:</div><div class="step__title">ABSCHLUSS DER RADONMESSUNG MIT ABSCHLIESSENDEM PRÜFBERICHT</div></div>
    </div>
    <p>Nach Ablauf der Messdauer, loggen Sie sich auf <span class="link">https://kundenportal.testoval.se/de</span> in Ihrem Account ein. Vermerken Sie hier das Ende der Messung und senden Sie anschließend alle Radondetektoren ausreichend frankiert in einem Umschlag oder einem Karton zeitnah an unsere Rücksendeadresse:</p>
    <div class="address">
      <svg width="30" height="22" viewBox="0 0 30 22" fill="none" stroke="#d3272e" stroke-width="1.8"><rect x="2" y="2" width="26" height="18"/><path d="M2 2 L15 12 L28 2M2 20 L12 10M28 20 L18 10"/></svg>
      <p>Luftprüfer.de<br>Lindenhofweg 7 – 28195 Musterstadt – Deutschland</p>
    </div>
    <p>Sobald die Radondetektoren im Labor von Testoval eingetroffen sind, werden diese fachgerecht analysiert und die Ergebnisse der Radonmessung ausgewertet. Ein vollständiger Prüfbericht wird Ihnen innerhalb 36 Stunden nach Erhalt der Detektoren im Labor per E-Mail zugeschickt.</p>
  </div>

  <div class="back-grey">
    <div class="tips">
      <h4>Weitere Hinweise:</h4>
      <div class="two">
        <ul class="bullets">
          <li>Bitte beachten Sie, dass die Radonmessung innerhalb von 15 Monaten nach Kaufdatum abgeschlossen sein muss.</li>
          <li>Versuchen Sie nicht das Gehäuse der Detektoren zu öffnen und platzieren Sie diese immer außer Reichweite von Kindern.</li>
          <li>Während der gesamten Messdauer dürfen die Detektoren nicht an einem anderen Ort umplatziert werden.</li>
        </ul>
        <ul class="bullets">
          <li>Durch die Anmeldung auf der Website <strong>https://kundenportal.testoval.se/de</strong> und die Eingabe der erforderlichen Daten bestätigt der/die Wohnungseigentümer*in/Messverantwortliche, dass er/sie die Messanleitung befolgt hat und die Detektoren gemäß den Anweisungen korrekt platziert wurden.</li>
        </ul>
      </div>
    </div>
  </div>
  <div class="back-foot">Datenschutz (GDPR), Impressum und AGBs: Mehr Information dazu finden Sie unter www.luftprüfer.de</div>
</section>

</body>
</html>
```